Coastline Premier Retreats Business Card Design

Design a business card for Coastline Premier Retreats. Look at the website for colors and reference. Card should have logo, name, title, office number, mobile number, email, URL and a tagline like, "Luxury Hotel & Resort Email Marketing" (This might change).

https://www.coastlinepremierretreats.example

The rest I will leave up to your imagination.

Contact Information for Business Card

Logo, name, title, office number, mobile number, email, URL and a tagline like, "Luxury Hotel & Resort Email Marketing" (This might change).

```html
<!DOCTYPE html>
<html lang="en">
<head>
<meta charset="UTF-8">
<title>Coastline Premier Retreats – Business Card</title>
<link href="https://fonts.googleapis.com/css2?family=Roboto:wght@400;700&display=swap" rel="stylesheet">
<style>
  :root{
    --backdrop:#2b2b2d;
    --orange:#e46a00;
    --paper:#f7f7f7;
    --ink:#151515;
    --muted:#666;
    --rule:#c9c9c9;
    --white:#ffffff;
  }
  *{margin:0;padding:0;box-sizing:border-box}
  html,body{width:1200px;height:912px;overflow:hidden}
  body{background:var(--backdrop);font-family:"Roboto",Arial,sans-serif;position:relative}

  .card{position:absolute;width:540px;height:310px;border-radius:18px;overflow:hidden;box-shadow:0 10px 24px rgba(0,0,0,.45)}

  /* front side */
  .card-front{left:90px;top:90px;background:var(--orange);display:flex;align-items:center;justify-content:center}
  .brand{display:flex;align-items:center;gap:12px;font-weight:700;color:var(--ink);text-transform:uppercase;letter-spacing:1px}
  .brand-mark{width:14px;height:14px;background:var(--ink);flex:none}
  .card-front .brand-name{font-size:27px}

  /* back side */
  .card-back{left:570px;top:510px;background:var(--paper)}
  .card-back .brand{position:absolute;left:30px;top:112px;width:200px;gap:10px}
  .card-back .brand-name{font-size:17px;line-height:1.25}
  .card-back .brand-mark{width:12px;height:12px;background:var(--orange)}

  .divider{position:absolute;left:248px;top:34px;width:1px;height:170px;background:var(--rule)}

  .contact{position:absolute;left:266px;top:40px;right:16px}
  .person-name{font-size:21px;font-weight:700;color:var(--ink)}
  .person-title{font-size:13px;color:var(--muted);margin-top:2px}
  .contact-list{list-style:none;margin-top:18px}
  .contact-list li{display:flex;align-items:center;gap:8px;font-size:12px;color:var(--ink);line-height:20px;white-space:nowrap}
  .contact-list svg{width:12px;height:12px;flex:none;fill:var(--orange)}

  .footer-rule{position:absolute;left:0;right:0;bottom:40px;height:3px;background:var(--ink)}
  .footer-band{position:absolute;left:0;right:0;bottom:0;height:37px;background:var(--orange);display:flex;align-items:center;justify-content:flex-end;padding-right:30px}
  .tagline{color:var(--white);font-size:14px}
</style>
</head>
<body>

  <section class="card card-front">
    <div class="brand">
      <span class="brand-mark"></span>
      <span class="brand-name">Coastline Premier Retreats</span>
    </div>
  </section>

  <section class="card card-back">
    <div class="brand">
      <span class="brand-mark"></span>
      <span class="brand-name">Coastline Premier Retreats</span>
    </div>

    <div class="divider"></div>

    <div class="contact">
      <p class="person-name">Daniel Reed</p>
      <p class="person-title">President</p>
      <ul class="contact-list">
        <li>
          <svg viewBox="0 0 24 24" aria-hidden="true"><path d="M6.6 10.8a15 15 0 0 0 6.6 6.6l2.2-2.2c.3-.3.7-.4 1-.2 1.1.4 2.3.6 3.6.6.6 0 1 .4 1 1V20c0 .6-.4 1-1 1A17 17 0 0 1 3 4c0-.6.4-1 1-1h3.5c.6 0 1 .4 1 1 0 1.3.2 2.5.6 3.6.1.3 0 .7-.2 1z"/></svg>
          555.014.2200
        </li>
        <li>
          <svg viewBox="0 0 24 24" aria-hidden="true"><path d="M7 1h10a2 2 0 0 1 2 2v18a2 2 0 0 1-2 2H7a2 2 0 0 1-2-2V3a2 2 0 0 1 2-2zm0 3v15h10V4zm5 16.2a.9.9 0 1 0 0 1.8.9.9 0 0 0 0-1.8z"/></svg>
          555.014.2201
        </li>
        <li>
          <svg viewBox="0 0 24 24" aria-hidden="true"><path d="M2 5h20v14H2zm2 2v.5l8 5 8-5V7zm0 2.8V17h16V9.8l-8 5z"/></svg>
          info@coastlinepremierretreats.example
        </li>
        <li>
          <svg viewBox="0 0 24 24" aria-hidden="true"><path d="M12 2a10 10 0 1 0 0 20 10 10 0 0 0 0-20zm-1 17.9A8 8 0 0 1 4.1 11H7c.1 3.3 1.6 6.4 4 8.9zM4.1 9A8 8 0 0 1 11 4.1C8.6 6.6 7.1 9.7 7 9zm8.9 10.9c2.4-2.5 3.9-5.6 4-8.9h2.9a8 8 0 0 1-6.9 8.9zM9 11h6c-.1 2.8-1.2 5.5-3 7.6-1.8-2.1-2.9-4.8-3-7.6zm0-2c.1-2.8 1.2-5.5 3-7.6 1.8 2.1 2.9 4.8 3 7.6zm8 0c-.1-2.1-.8-4.1-1.9-5.9A8 8 0 0 1 19.9 9z"/></svg>
          www.coastlinepremierretreats.example
        </li>
      </ul>
    </div>

    <div class="footer-rule"></div>
    <div class="footer-band">
      <span class="tagline">Luxury Hotel &amp; Resort Email Marketing</span>
    </div>
  </section>

</body>
</html>
```